LinkedIn Banner Design for B2B Consulting Firm

Take the already developed logo (attached) and incorporate it into a creative banner design for placement on LinkedIn (the social media platform targeting business users). The banner will be used on the firm's company profile page on LinkedIn (not yet created).

```html
<!DOCTYPE html>
<html lang="en">
<head>
<meta charset="UTF-8">
<title>Fractional Marketing Services – LinkedIn Banner</title>
<link href="https://fonts.googleapis.com/css2?family=Bebas+Neue&family=Poppins:wght@500;600&display=swap" rel="stylesheet">
<style>
  :root {
    --page-bg: #ffffff;
    --banner-grey: #d9d9d9;
    --banner-grey-mid: #cdcdcd;
    --banner-grey-dark: #bdbdbd;
    --ink-green: #22382a;
    --banner-shadow: rgba(0, 0, 0, 0.28);
  }
  html, body {
    margin: 0;
    padding: 0;
    width: 1200px;
    height: 418px;
    overflow: hidden;
    background: var(--page-bg);
  }
  .banner {
    position: absolute;
    left: 66px;
    top: 110px;
    width: 1059px;
    height: 180px;
    overflow: hidden;
    box-shadow: 0 6px 14px var(--banner-shadow);
  }
  .banner-backdrop {
    position: absolute;
    inset: 0;
    background:
      linear-gradient(90deg,
        var(--banner-grey) 0%, var(--banner-grey-dark) 6%, var(--banner-grey) 12%,
        var(--banner-grey-mid) 20%, var(--banner-grey-dark) 26%, var(--banner-grey) 33%,
        var(--banner-grey-mid) 40%, var(--banner-grey) 46%, var(--banner-grey-dark) 55%,
        var(--banner-grey) 62%, var(--banner-grey-mid) 72%, var(--banner-grey) 80%,
        var(--banner-grey-dark) 90%, var(--banner-grey) 100%);
  }
  .headline {
    position: absolute;
    left: 214px;
    top: 57px;
    margin: 0;
  }
  .headline-title {
    display: block;
    font-family: "Bebas Neue", sans-serif;
    font-weight: 400;
    font-size: 34px;
    line-height: 1;
    color: var(--ink-green);
    letter-spacing: 0.1px;
  }
  .headline-audience {
    display: block;
    margin-top: 3px;
    font-family: "Poppins", sans-serif;
    font-weight: 500;
    font-size: 16.2px;
    line-height: 17px;
    color: var(--ink-green);
  }
  .photo-strip {
    position: absolute;
    left: 0;
    top: 0;
  }
</style>
</head>
<body>
  <section class="banner">
    <div class="banner-backdrop" role="img" aria-label="Faded grey office scene with silhouettes of business people shaking hands and a faint network of connected lines"></div>

    <h1 class="headline">
      <span class="headline-title">Fractional Marketing Services</span>
      <span class="headline-audience">FOR PRIVATE EQUITY FUNDS, FAMILY OFFICES<br>&amp; INVESTMENT BANKS</span>
    </h1>

    <svg class="photo-strip" width="1059" height="180" viewBox="0 0 1059 180">
      <defs>
        <linearGradient id="lounge-tones" x1="0" y1="0" x2="0" y2="1">
          <stop offset="0" stop-color="#eef1f2"/>
          <stop offset="0.55" stop-color="#b7c0c4"/>
          <stop offset="1" stop-color="#4a4644"/>
        </linearGradient>
        <linearGradient id="meeting-tones" x1="0" y1="0" x2="0" y2="1">
          <stop offset="0" stop-color="#e4eaee"/>
          <stop offset="0.5" stop-color="#a9b3b8"/>
          <stop offset="1" stop-color="#7d878c"/>
        </linearGradient>
        <linearGradient id="desk-tones" x1="0" y1="0" x2="0" y2="1">
          <stop offset="0" stop-color="#eaeef0"/>
          <stop offset="0.6" stop-color="#b0babf"/>
          <stop offset="1" stop-color="#5b6166"/>
        </linearGradient>
      </defs>
      <polygon points="699,15 809,15 735,149 619,149" fill="url(#lounge-tones)" role="img" aria-label="Bright office lounge with sofa and tall windows"/>
      <polygon points="935,16 1038,16 963,150 843,150" fill="url(#desk-tones)" role="img" aria-label="Colleague working at a desk by the windows"/>
      <polygon points="804,36 912,36 840,169 721,169" fill="url(#meeting-tones)" role="img" aria-label="Team meeting around a desk in an open office"/>
    </svg>
  </section>
</body>
</html>
```